K & R Acre Works. Business card design

We need a business card designed for a new business. We have a bulldozer and tractor service. We clear land and make wildlife food plots. We provide disking, bush hogging, and site prep services.
I have attached an image of a business card that I like and would like my business cards to look similar.

Target Market(s)

anyone needing bulldozer and/or tractor services

Industry/Entity Type

Business

Contact Information for Business Card

K & R Acre Works, Operated by 7-T-Ranch
Wade Colton
601-472-3358
wcr4817@fieldmail-example.com

Font styles to use
Sans Serif

Colors

Designer to choose colors to be used in the design.

Requirements
Must have
• image of tractor and bulldozer
• Land Clearing
• Wildlife food plots
• Bush Hogging
• Disking
• Site prep
Nice to have
• i have included a image of a business card that i like. I would like mine to be similar.

```html
<!DOCTYPE html>
<html lang="en">
<head>
<meta charset="UTF-8">
<title>K &amp; R Acre Works – Business Card</title>
<link rel="stylesheet" href="https://fonts.googleapis.com/css2?family=Roboto:wght@400;500;700&family=Roboto+Condensed:wght@700&display=swap">
<style>
  :root {
    --page-bg: #2b2b2b;
    --card-bg: #f2f2f1;
    --olive: #8f8d2b;
    --olive-band: #9a9a2e;
    --brown: #6b3f14;
    --text-dark: #444444;
    --text-black: #222222;
    --divider: #cfcfcf;
    --photo-dozer: #6e7a55;
    --photo-tractor: #9b7a4a;
    --white: #ffffff;
  }
  * { margin: 0; padding: 0; box-sizing: border-box; }
  html, body {
    width: 1200px; height: 960px; overflow: hidden;
    background: var(--page-bg);
    font-family: "Roboto", Arial, sans-serif;
  }
  .business-card {
    position: absolute; left: 300px; top: 310px;
    width: 600px; height: 342px;
    background: var(--card-bg);
    border-radius: 18px;
    overflow: hidden;
  }
  .brand-name {
    position: absolute; left: 84px; top: 102px;
    font-family: "Roboto Condensed", "Arial Narrow", sans-serif;
    font-weight: 700; font-size: 23px; letter-spacing: 0.6px;
    color: var(--brown); text-transform: uppercase; line-height: 1;
    white-space: nowrap;
  }
  .brand-tagline {
    position: absolute; left: 84px; top: 128px;
    font-family: "Roboto Condensed", "Arial Narrow", sans-serif;
    font-weight: 700; font-size: 10.4px; color: var(--text-black);
    text-transform: uppercase; line-height: 1; white-space: nowrap;
  }
  .service-photo { position: absolute; top: 145px; height: 75px; }
  .service-photo--dozer {
    left: 84px; width: 127px;
    background: linear-gradient(160deg, #55683f 0%, var(--photo-dozer) 55%, #8a7d5c 100%);
  }
  .service-photo--tractor {
    left: 216px; width: 102px;
    background: linear-gradient(160deg, #5f7443 0%, var(--photo-tractor) 60%, #a58d5e 100%);
  }
  .card-divider {
    position: absolute; left: 348px; top: 70px;
    width: 1px; height: 185px; background: var(--divider);
  }
  .contact-name {
    position: absolute; left: 375px; top: 67px;
    font-weight: 700; font-size: 21px; color: var(--olive);
    text-transform: uppercase; line-height: 1.1; white-space: nowrap;
  }
  .contact-role {
    position: absolute; left: 375px; top: 92px;
    font-weight: 500; font-size: 15px; color: var(--brown); line-height: 1;
  }
  .contact-details {
    position: absolute; left: 377px; top: 114px;
    font-size: 13px; color: var(--text-dark); line-height: 18px; list-style: none;
    white-space: nowrap;
  }
  .contact-details li:first-child { font-size: 14.5px; }
  .services-heading {
    position: absolute; left: 375px; top: 161px;
    font-weight: 700; font-size: 17px; color: var(--olive); line-height: 1.1;
  }
  .services-list {
    position: absolute; left: 375px; top: 181px;
    list-style: none; font-size: 14.5px; color: var(--text-dark); line-height: 18px;
    white-space: nowrap;
  }
  .services-list li::before,
  .services-list .inline-sep::before {
    content: "•"; color: var(--olive); margin-right: 6px; font-size: 13px;
  }
  .services-list .inline-sep::before { margin: 0 3px 0 4px; }
  .card-footer { position: absolute; left: 0; top: 297px; width: 600px; height: 45px; }
  .website {
    position: absolute; right: 14px; top: 311px;
    font-weight: 500; font-size: 14px; letter-spacing: 2px; line-height: 18px;
    color: var(--white); text-transform: uppercase; white-space: nowrap;
  }
</style>
</head>
<body>
  <div class="business-card">
    <div class="brand-name">K &amp; R Acre Works</div>
    <div class="brand-tagline">For all of your land improvement needs</div>
    <div class="service-photo service-photo--dozer" role="img" aria-label="Photo of a bulldozer clearing land"></div>
    <div class="service-photo service-photo--tractor" role="img" aria-label="Photo of a tractor with a mower in a field"></div>

    <div class="card-divider"></div>

    <div class="contact-name">Wade Colton</div>
    <div class="contact-role">OWNER</div>
    <ul class="contact-details">
      <li>601-472-3358</li>
      <li>wcr4817@fieldmail-example.com</li>
    </ul>

    <div class="services-heading">WE CREADED</div>
    <ul class="services-list">
      <li>Land Clearing</li>
      <li>Wildlife food plots</li>
      <li>Bush Hogging</li>
      <li>Disking<span class="inline-sep"></span>Site prep</li>
    </ul>

    <svg class="card-footer" viewBox="0 0 600 45" aria-hidden="true">
      <rect x="0" y="23" width="336" height="12" fill="var(--brown)"/>
      <rect x="0" y="35" width="600" height="10" fill="var(--olive-band)"/>
      <path d="M318,45 L318,35 C330,35 340,0 368,0 L600,0 L600,45 Z" fill="var(--white)"/>
      <path d="M322,45 L322,37 C334,37 344,2 370,2 L600,2 L600,45 Z" fill="var(--olive-band)"/>
    </svg>
    <div class="website">www.kr-acres.example</div>
  </div>
</body>
</html>
```